Harborline Lending and Capital. We provide MOSTLY residential home mortgages in Florida AND commercial loans for investment properties throughout the United states.
I would love to emulate so of the lender sites that are available on the internet but I would like to have the site as popular as possible for SEO purposes. Clients can already click the link to take them to the mortgage application where they can complete that and upload documents. If you could polish that up for me that would be great. I can also provide you with great detail on loan programs that are currently being offered. WE OFFER ALL MORTGAGE LENDING PRODUCTS. I would also like to add something in reference to the rate but I don't think it's legal to actually state or promise a rate for mortgage since they vary based on loan type, client and other criteria...

On the Harborline real estate site I would like to add a link or some way for clients to be able to put in credit card information to render services ...

Please let me know what you need from me

Thank you !!

Current link to site to improve and code

https://harborlinelendingandcapital.example/

Industry/Entity Type

Residential and commmercial lending

Coding

Coded - Design and coding required

Number of Pages Required

2 page

Requirements
Must have
• Love to integrate Mortgage interest rates even if general
Nice to have
• Link to fill out mortgage application via Quorvel LPX software

```html
<!DOCTYPE html>
<html lang="en">
<head>
<meta charset="utf-8">
<title>Harborline Lending and Capital — Home</title>
<link href="https://fonts.googleapis.com/css2?family=Montserrat:wght@400;500;600;700;800&family=Crimson+Text:wght@600&display=swap" rel="stylesheet">
<style>
:root{
  --green:#8db83a;
  --green-dark:#1b2e17;
  --forest:#23391f;
  --mint:#e5f0e3;
  --ink:#1e2a1b;
  --text:#4a4a4a;
  --white:#ffffff;
  --line:#d6d6d6;
}
*{box-sizing:border-box;margin:0;padding:0}
html,body{width:1200px;height:4084px;overflow:hidden}
body{font-family:"Montserrat",sans-serif;color:var(--ink);background:var(--white);position:relative}
.abs{position:absolute}
a{color:inherit;text-decoration:none}
.btn{position:absolute;display:flex;align-items:center;justify-content:center;background:var(--green);color:var(--white);font-weight:700;font-size:13px;border-radius:30px;letter-spacing:.2px}
.eyebrow{font-size:14px;font-weight:700;color:var(--green);display:flex;align-items:center;gap:8px;text-transform:uppercase}
.eyebrow .dot{width:14px;height:14px;border-radius:50%;background:var(--forest)}
.heading{font-weight:700;font-size:28px;text-transform:uppercase;color:var(--ink);letter-spacing:.3px}
.center{left:0;width:1200px;text-align:center;justify-content:center}
.lead{font-size:13.5px;line-height:22px;color:var(--text)}

/* header */
.site-header{top:0;left:0;width:1200px;height:108px;background:var(--white)}
.brand{display:flex;align-items:center;gap:12px}
.brand .mark{width:46px;height:46px;border-radius:50%;background:var(--forest)}
.brand .name{font-size:11px;font-weight:700;color:var(--ink);letter-spacing:.6px;text-transform:uppercase}
.nav a{position:absolute;top:46px;font-size:14px;color:#333}
.nav a.active{color:var(--green);font-weight:600}
.call{left:925px;top:32px;display:flex;align-items:center;gap:14px}
.call .ring{width:44px;height:44px;border-radius:50%;background:var(--green);box-shadow:0 0 0 5px #e4efd4;display:flex;align-items:center;justify-content:center}
.call b{display:block;font-size:13px}
.call span{font-size:13px;color:#333}

/* hero */
.hero{top:108px;left:0;width:1200px;height:599px;background:linear-gradient(180deg,#5d6b4f 0%,#3f5a3c 35%,#2e4b33 70%,#22362a 100%)}
.hero-kicker{top:278px;left:0;width:1200px;text-align:center;font-size:13px;font-weight:700;color:var(--white)}
.hero-title{top:307px;left:0;width:1200px;text-align:center;font-size:38px;font-weight:800;color:var(--white);line-height:50px}

/* about */
.about-photo{left:133px;top:792px;width:412px;height:412px;border-radius:50%;background:linear-gradient(160deg,#e8a06a 0%,#b98aa0 35%,#4d6e8a 65%,#2f5a35 100%);box-shadow:10px 0 0 0 var(--green)}
.about-text{left:640px;top:822px;width:450px}
.about-text .heading{margin:10px 0 16px;line-height:36px}
.about-text p{font-size:13.5px;line-height:22px;color:var(--text);margin-bottom:8px}

/* products */
.card{position:absolute;top:1510px;width:422px;height:314px;border-radius:16px;text-align:center;color:var(--white)}
.card.light{left:169px;background:var(--green)}
.card.dark{left:610px;background:var(--green-dark)}
.card .badge{position:absolute;left:151px;top:-60px;width:120px;height:120px;border-radius:50%;border:7px solid var(--white);display:flex;align-items:center;justify-content:center}
.card.light .badge{background:var(--green)}
.card.dark .badge{background:var(--green-dark)}
.card h3{position:absolute;left:0;top:90px;width:100%;font-size:17px;font-weight:700;line-height:25px;text-transform:uppercase;white-space:nowrap}
.card p{position:absolute;left:34px;top:152px;width:354px;font-size:13px;line-height:22px}
.card .more{position:absolute;left:148px;top:234px;width:127px;height:41px;border-radius:30px;font-size:13px;font-weight:700;display:flex;align-items:center;justify-content:center}
.card.light .more{border:1.5px solid var(--white)}
.card.dark .more{background:var(--green)}

/* properties */
.properties{top:1905px;left:0;width:1200px;height:634px;background:var(--mint)}
.prop{position:absolute;top:2125px;width:237px;height:279px;border-radius:8px;overflow:hidden}
.prop .label{position:absolute;left:0;width:100%;bottom:30px;text-align:center;color:var(--white);font-size:17px;font-weight:500;display:flex;justify-content:center;align-items:center;gap:5px;white-space:nowrap}

/* rates */
.rate{position:absolute;top:2800px;width:170px;height:170px;border-radius:50%;background:var(--white);border:2px solid #e3e3e3;box-shadow:0 4px 10px rgba(0,0,0,.12);text-align:center}
.rate .dot{width:38px;height:38px;border-radius:50%;background:var(--forest);margin:30px auto 8px}
.rate b{display:block;font-size:22px;color:var(--green);font-weight:700}
.rate span{font-family:"Crimson Text",serif;font-size:12px;color:#222}

/* calculator */
.calculator{top:3048px;left:0;width:1200px;height:594px;background:linear-gradient(180deg,#2a4326,#1f3520)}
.calc-label{font-size:15px;font-weight:500;color:var(--white)}
.select{position:absolute;width:393px;height:49px;background:var(--white);border-radius:6px}
.select svg{position:absolute;right:22px;top:20px}

/* footer */
.newsletter-title{left:505px;top:3722px;font-size:18px;font-weight:600;color:var(--ink)}
.subscribe{left:658px;top:3712px;width:434px;height:41px;border-radius:30px;background:#ececec;display:flex;align-items:center}
.subscribe span{padding-left:25px;font-size:13px;color:#555;flex:1}
.subscribe b{width:114px;height:41px;border-radius:30px;background:var(--green);color:var(--white);font-size:13px;display:flex;align-items:center;justify-content:center}
.rule{left:104px;width:992px;height:1px;background:var(--line)}
.fcol h4{font-size:16px;font-weight:700;color:var(--ink);margin-bottom:14px;text-transform:uppercase}
.fcol li{list-style:none;font-size:13px;color:#222;height:30.5px;white-space:nowrap}
.social{display:flex;gap:10px}
.social i{width:34px;height:34px;border-radius:50%;border:1.5px solid var(--ink);display:block}
.social i:first-child{background:var(--forest);border-color:var(--forest)}
.copyright{top:4043px;font-size:13px;color:#444}
.copyright a{text-decoration:underline}
</style>
</head>
<body>

<header class="abs site-header">
  <div class="abs brand" style="left:104px;top:31px">
    <div class="mark"></div>
    <div class="name">Harborline Lending and Capital</div>
  </div>
  <nav class="nav">
    <a class="active" href="#" style="left:455px">Home</a>
    <a href="#" style="left:530px">About</a>
    <a href="#" style="left:607px">Properties</a>
    <a href="#" style="left:696px">Mortgage Lending Products</a>
  </nav>
  <div class="abs call">
    <div class="ring">
      <svg width="18" height="18" viewBox="0 0 24 24"><path fill="#fff" d="M6.6 10.8a15 15 0 0 0 6.6 6.6l2.2-2.2c.3-.3.7-.4 1-.2 1.1.4 2.3.6 3.6.6.6 0 1 .4 1 1V20c0 .6-.4 1-1 1A17 17 0 0 1 3 4c0-.6.4-1 1-1h3.5c.6 0 1 .4 1 1 0 1.3.2 2.5.6 3.6.1.3 0 .7-.2 1z"/></svg>
    </div>
    <div><b>Call Us Today!</b><span>+1 555 014 2290</span></div>
  </div>
</header>

<section class="abs hero" role="img" aria-label="Aerial photo of waterfront Florida homes on a green peninsula"></section>
<div class="abs hero-kicker">WELCOME TO HARBORLINE LENDING AND CAPITAL FLORIDA</div>
<h1 class="abs hero-title">YOUR BEST RESOURCE FOR HASSLE-FREE,<br>LOW COST MORTGAGE ORIGINATION</h1>
<a class="btn" href="#" style="left:393px;top:433px;width:460px;height:41px">FILL OUT MORTGAGE APPLICATION TO BEGIN LENDING PR</a>

<section aria-label="About us">
  <div class="abs about-photo" role="img" aria-label="City skyline at sunset with palm trees"></div>
  <div class="abs about-text">
    <div class="eyebrow">About Us <span class="dot"></span></div>
    <h2 class="heading">Harborline Lending and<br>Capital Florida</h2>
    <p>Harborline Lending Originates Residential Home loans in Florida and Commercial and business financing in all 50 States. We have over 25 years of experience in ALL types of real estate and commercial lending.</p>
    <p>We are strategically partnered to help you obtain ALL necessary components of residential and commercial lending. From the RIGHT lending partners to the best practice Insurance avenues and commercial and residential real estate partners</p>
  </div>
  <a class="btn" href="#" style="left:640px;top:1136px;width:126px;height:42px">READ MORE</a>
</section>

<section aria-label="Mortgage lending products">
  <div class="abs eyebrow center" style="top:1292px;display:flex">We Offer All <span class="dot"></span></div>
  <h2 class="abs heading" style="top:1318px;left:0;width:1200px;text-align:center">Mortgage Lending Products</h2>
  <p class="abs lead" style="top:1368px;left:210px;width:780px;text-align:center">Lorem ipsum dolor sit amet, consectetur adipiscing elit, sed do eiusmod tempor incididunt ut labore et dolore magna aliqua. Ut enim ad minim veniam, quis nostrud exercitation ullamco laboris nisi ut aliquip ex consequat.</p>

  <article class="card light">
    <div class="badge">
      <svg width="62" height="62" viewBox="0 0 64 64" fill="none" stroke="#fff" stroke-width="4" stroke-linejoin="round"><path d="M6 30 32 8l26 22"/><path d="M13 26v30h38V26"/><circle cx="32" cy="40" r="9"/><path d="M32 34v12" stroke-width="3"/></svg>
    </div>
    <h3>Residential Home Mortgages<br>in Florida</h3>
    <p>Lorem ipsum dolor sit amet, consectetur adipiscing elit, sed do eiusmod tempor incididunt ut labore et dolore magna aliqua.</p>
    <a class="more" href="#">READ MORE</a>
  </article>

  <article class="card dark">
    <div class="badge">
      <svg width="66" height="62" viewBox="0 0 66 62" fill="#8db83a"><rect x="6" y="40" width="8" height="18"/><rect x="18" y="30" width="8" height="28"/><rect x="30" y="22" width="8" height="36"/><rect x="42" y="14" width="8" height="44"/><rect x="54" y="6" width="8" height="52"/><rect x="2" y="58" width="62" height="3"/></svg>
    </div>
    <h3>Commercial Loans for Investment<br>Properties</h3>
    <p>Lorem ipsum dolor sit amet, consectetur adipiscing elit, sed do eiusmod tempor incididunt ut labore et dolore magna aliqua.</p>
    <a class="more" href="#">READ MORE</a>
  </article>
</section>

<section class="abs properties" aria-label="Exclusive properties"></section>
<div class="abs eyebrow" style="left:103px;top:2005px">Properties <span class="dot"></span></div>
<h2 class="abs heading" style="left:103px;top:2033px">Our Exclusive Properties</h2>
<a class="btn" href="#" style="left:968px;top:2008px;width:126px;height:41px">VIEW MORE</a>

<div class="prop" style="left:104px;background:linear-gradient(180deg,#cfd3d6,#8c8f92 60%,#3b3d3f)" role="img" aria-label="Modern grey house exterior"><div class="label"><svg width="12" height="16" viewBox="0 0 12 16"><path fill="#fff" d="M6 0a6 6 0 0 0-6 6c0 4.5 6 10 6 10s6-5.5 6-10a6 6 0 0 0-6-6zm0 8.5A2.5 2.5 0 1 1 6 3.5a2.5 2.5 0 0 1 0 5z"/></svg>12 Sunset Street</div></div>
<div class="prop" style="left:353px;background:linear-gradient(180deg,#3c4a52,#1c2733 60%,#0f151b)" role="img" aria-label="Dark modern house at dusk"><div class="label"><svg width="12" height="16" viewBox="0 0 12 16"><path fill="#fff" d="M6 0a6 6 0 0 0-6 6c0 4.5 6 10 6 10s6-5.5 6-10a6 6 0 0 0-6-6zm0 8.5A2.5 2.5 0 1 1 6 3.5a2.5 2.5 0 0 1 0 5z"/></svg>34 Union Avenue</div></div>
<div class="prop" style="left:603px;background:linear-gradient(180deg,#8ea4b6,#8b7a62 55%,#2b2d2a)" role="img" aria-label="Contemporary house with pool"><div class="label"><svg width="12" height="16" viewBox="0 0 12 16"><path fill="#fff" d="M6 0a6 6 0 0 0-6 6c0 4.5 6 10 6 10s6-5.5 6-10a6 6 0 0 0-6-6zm0 8.5A2.5 2.5 0 1 1 6 3.5a2.5 2.5 0 0 1 0 5z"/></svg>56 Washington Street</div></div>
<div class="prop" style="left:852px;background:linear-gradient(90deg,#7a3d2e,#5b3028 55%,#2f3a48)" role="img" aria-label="House with timber facade"><div class="label"><svg width="12" height="16" viewBox="0 0 12 16"><path fill="#fff" d="M6 0a6 6 0 0 0-6 6c0 4.5 6 10 6 10s6-5.5 6-10a6 6 0 0 0-6-6zm0 8.5A2.5 2.5 0 1 1 6 3.5a2.5 2.5 0 0 1 0 5z"/></svg>78 Oak Boulevard</div></div>
<div class="prop" style="left:1102px;background:linear-gradient(180deg,#7fa6d2,#a0694a 55%,#6e6e6e)" role="img" aria-label="Suburban house with garage"><div class="label" style="justify-content:flex-start;padding-left:40px"><svg width="12" height="16" viewBox="0 0 12 16"><path fill="#fff" d="M6 0a6 6 0 0 0-6 6c0 4.5 6 10 6 10s6-5.5 6-10a6 6 0 0 0-6-6zm0 8.5A2.5 2.5 0 1 1 6 3.5a2.5 2.5 0 0 1 0 5z"/></svg>12 Sunrise Lane</div></div>

<section aria-label="Rates">
  <div class="abs eyebrow center" style="top:2636px;display:flex">Rates <span class="dot"></span></div>
  <h2 class="abs heading" style="top:2662px;left:0;width:1200px;text-align:center">With Rates or Rates</h2>
  <p class="abs lead" style="top:2712px;left:210px;width:780px;text-align:center">Lorem ipsum dolor sit amet, consectetur adipiscing elit, sed do eiusmod tempor incididunt ut labore et dolore magna aliqua. Ut enim ad minim veniam, quis nostrud exercitation ullamco laboris nisi ut aliquip ex consequat.</p>
  <div class="rate" style="left:169px"><div class="dot"></div><b>6.52%</b><span>15-Year Fixed Rate</span></div>
  <div class="rate" style="left:398px"><div class="dot"></div><b>7.19%</b><span>20-Year Fixed Rate</span></div>
  <div class="rate" style="left:630px"><div class="dot"></div><b>7.31%</b><span>30-Year Fixed Rate</span></div>
  <div class="rate" style="left:860px"><div class="dot"></div><b>7.07%</b><span>30-Year Fixed Rate</span></div>
</section>

<section class="abs calculator" aria-label="Mortgage calculator"></section>
<div class="abs eyebrow center" style="top:3149px;display:flex;color:#fff">Calculator <span class="dot" style="background:#fff"></span></div>
<h2 class="abs heading" style="top:3177px;left:0;width:1200px;text-align:center;color:#fff">Mortgage Calculator</h2>
<div class="abs calc-label" style="left:190px;top:3248px">Period Of Time</div>
<div class="abs calc-label" style="left:606px;top:3248px">Rate Of Interest</div>
<div class="select" style="left:174px;top:3284px"><svg width="12" height="8" viewBox="0 0 12 8"><path d="M1 1l5 5 5-5" stroke="#333" stroke-width="1.8" fill="none"/></svg></div>
<div class="select" style="left:590px;top:3284px"><svg width="12" height="8" viewBox="0 0 12 8"><path d="M1 1l5 5 5-5" stroke="#333" stroke-width="1.8" fill="none"/></svg></div>
<div class="abs calc-label" style="left:190px;top:3361px">Loan Amount</div>
<div class="abs calc-label" style="left:606px;top:3361px">Down Payment</div>
<div class="select" style="left:174px;top:3397px"><svg width="12" height="8" viewBox="0 0 12 8"><path d="M1 1l5 5 5-5" stroke="#333" stroke-width="1.8" fill="none"/></svg></div>
<div class="select" style="left:590px;top:3397px"><svg width="12" height="8" viewBox="0 0 12 8"><path d="M1 1l5 5 5-5" stroke="#333" stroke-width="1.8" fill="none"/></svg></div>
<a class="btn" href="#" style="left:393px;top:3492px;width:460px;height:41px">FILL OUT MORTGAGE APPLICATION TO BEGIN LENDING PR</a>

<footer>
  <div class="abs brand" style="left:108px;top:3710px">
    <div class="mark"></div>
    <div class="name" style="font-size:10.5px">Harborline Lending and Capital</div>
  </div>
  <div class="abs newsletter-title">NEWSLETTER</div>
  <div class="abs subscribe"><span>Enter Your Email</span><b>SUBMIT</b></div>
  <div class="abs rule" style="top:3791px"></div>

  <div class="abs fcol" style="left:108px;top:3822px">
    <h4>Quick Links</h4>
    <ul><li>Home</li><li>About</li><li>Properties</li><li>Mortgage Lending Products</li><li>Contact Us</li></ul>
  </div>
  <div class="abs fcol" style="left:330px;top:3822px">
    <h4>Contact Us</h4>
    <ul><li>+1 555 014 2290</li><li>info@harborlinelending.example</li></ul>
  </div>
  <div class="abs fcol" style="left:659px;top:3822px">
    <h4>Adderess</h4>
    <ul><li>No: 14 Harbor Way, Florida</li><li>Harborline Lending and Capital</li></ul>
  </div>
  <div class="abs fcol" style="left:938px;top:3822px">
    <h4>Follow Us</h4>
    <div class="social"><i></i><i></i><i></i><i></i></div>
  </div>

  <div class="abs rule" style="top:4026px"></div>
  <div class="abs copyright" style="left:0;width:1200px;text-align:center">© 2025 <a href="#">Harborline Lending and Capital</a> | All Rights Reserved</div>
</footer>

</body>
</html>
```